Biz Card

MARKETING today is the most rapidly changing business discipline. Media options to reach customers, actual customer preferences and consumer buying decisions change by the minute . . . no, by the second. The behavioral data generated by all aspects of the business and the new technologies that put the data to work together produce the potential to generate business intelligence and guide smart resource allocation to influence purchase and retention. However, to realize this potential, marketing professionals at all levels and in all organizations must continuously improve their skills not just from on-the-job training but by learning from masters in the field. The Bright Horizon Guild is the training center that serves this professional development need.model logos:msi.orgama.orgcontentmarketinginstitute.comBook covers on MarketingMetrics, Marketing Anaytics
Industry/Entity Type
Business
Contact Information for Business Card
Roy A. YoungCEOMarketing Science Academyphone: 310-601-4755email: roy@marketingscience.comAddress:437 South Rexford DriveBeverly Hills, CA 89377
Look and feel
Each slider illustrates characteristics of the customer's brand and the style your logo design should communicate.

```html
<!DOCTYPE html>
<html lang="en">
<head>
<meta charset="utf-8">
<title>Bright Horizon Guild — Business Card</title>
<link href="https://fonts.googleapis.com/css2?family=Open+Sans:wght@400;700;800&family=Roboto+Condensed:wght@400;700&display=swap" rel="stylesheet">
<style>
  :root {
    --backdrop: #e9e8e8;
    --navy: #243c77;
    --navy-text: #1f3a7a;
    --orange: #e47b22;
    --white: #ffffff;
    --paper: #fbfbfb;
    --divider: #9aa0ad;
  }
  * { margin: 0; padding: 0; box-sizing: border-box; }
  html, body { width: 1200px; height: 1200px; overflow: hidden; }
  body { background: var(--backdrop); position: relative; font-family: "Open Sans", Arial, sans-serif; }

  .card { position: absolute; width: 713px; height: 420px; }

  /* Front */
  .card-front { left: 238px; top: 117px; background: var(--navy); color: var(--white); }
  .front-brand {
    position: absolute; left: 0; right: 0; top: 95px;
    display: flex; align-items: center; justify-content: center; gap: 22px;
  }
  .brand-dot { width: 34px; height: 34px; border-radius: 50%; background: var(--white); }
  .front-brand .brand-name {
    font-weight: 800; font-size: 44px; letter-spacing: 1px; line-height: 1; text-transform: uppercase;
  }
  .tagline-band {
    position: absolute; left: 0; right: 0; top: 269px; height: 50px;
    background: var(--orange); display: flex; align-items: center; justify-content: center;
    font-size: 17px; color: var(--white);
  }
  .front-url {
    position: absolute; left: 0; right: 0; top: 352px; text-align: center; font-size: 17px;
  }

  /* Back */
  .card-back { left: 230px; top: 644px; width: 712px; height: 417px; background: var(--paper); }
  .back-brand {
    position: absolute; left: 83px; top: 120px; width: 240px;
    display: flex; flex-direction: column; align-items: flex-start; gap: 14px;
  }
  .back-brand .brand-dot { background: var(--orange); width: 40px; height: 40px; }
  .back-brand .brand-name {
    font-weight: 800; font-size: 34px; line-height: 1.05; color: var(--orange); text-transform: uppercase;
  }
  .contact { position: absolute; left: 399px; top: 113px; color: var(--navy-text); font-family: "Roboto Condensed", Arial, sans-serif; }
  .contact-name { font-weight: 700; font-size: 27px; line-height: 1; }
  .contact-role { font-family: "Open Sans", Arial, sans-serif; font-size: 15px; margin-top: 13px; margin-left: 2px; }
  .contact-address { font-size: 17px; line-height: 24px; margin-top: 28px; margin-left: 2px; }
  .contact-line { display: flex; align-items: center; gap: 16px; font-size: 17px; line-height: 24px; margin-left: 2px; }
  .contact-line svg { width: 18px; height: 14px; flex: none; }
</style>
</head>
<body>
  <section class="card card-front">
    <div class="front-brand">
      <span class="brand-dot"></span>
      <span class="brand-name">Bright Horizon Guild</span>
    </div>
    <div class="tagline-band">Executive Education in Marketing Analtics and Technology</div>
    <div class="front-url">www.brighthorizonguild.com</div>
  </section>

  <section class="card card-back">
    <div class="back-brand">
      <span class="brand-dot"></span>
      <span class="brand-name">Bright<br>Horizon<br>Guild</span>
    </div>
    <div class="contact">
      <div class="contact-name">Neil P. Barton</div>
      <div class="contact-role">CEO</div>
      <div class="contact-address">912 North Calloway Lane<br>Beverly Hills, CA 89377</div>
      <div class="contact-line" style="margin-top:5px">
        <svg viewBox="0 0 18 14" aria-hidden="true"><path fill="#e47b22" d="M1 5c0-3 16-3 16 0v2h-4V5H5v2H1zM4 7h10l2 6H2z"/><circle cx="9" cy="10" r="1.8" fill="#fbfbfb"/></svg>
        <span>310-555-0182</span>
      </div>
      <div class="contact-line">
        <svg viewBox="0 0 18 14" aria-hidden="true"><rect x="1" y="2" width="16" height="11" fill="#e47b22"/><path d="M1 2l8 6 8-6" fill="none" stroke="#fbfbfb" stroke-width="1.4"/></svg>
        <span>neil@brighthorizonguild.com</span>
      </div>
    </div>
  </section>
</body>
</html>
```